Folder Design: Mobile Laboratory Service

Need a folder designed for a Mobile Laboratory Service. Folder needs to be very professional and will be used to hold brochure, contract and business card of business. Logos of the company are attached.

Industry/Entity Type

Healthcare

```html
<!DOCTYPE html>
<html lang="en">
<head>
<meta charset="utf-8">
<title>Coastline Mobile Labs – Presentation Folder</title>
<link rel="stylesheet" href="https://fonts.googleapis.com/css2?family=Montserrat:wght@500;600;800;900&family=Poppins:wght@400;500&display=swap">
<style>
  :root{
    --stage:#8a8a8a;
    --navy:#0b2a63;
    --blue:#1a4f9c;
    --royal:#2367b8;
    --sky:#5fa6dc;
    --paper:#ffffff;
    --paper-shade:#ececee;
    --ink:#3a3f4a;
    --brand:#1f5fb5;
    --rule:#c9ced8;
  }
  *{margin:0;padding:0;box-sizing:border-box}
  html,body{width:1200px;height:2163px;overflow:hidden;background:var(--stage)}
  .folder{position:absolute;left:40px;top:504px;width:1120px;height:1154px}
  .folder-art{position:absolute;left:0;top:0;width:1120px;height:1154px}
  .trim{position:absolute;top:7px;height:757px;border:1px solid var(--rule);border-bottom:none;opacity:.6}
  .trim--back{left:9px;width:544px}
  .trim--front{left:570px;width:543px}

  .photo{position:absolute;border-radius:50%;box-shadow:0 6px 18px rgba(0,0,0,.35)}
  .photo--sample{left:46px;top:51px;width:198px;height:198px;background:radial-gradient(circle at 45% 45%,#f3d6e4 0 18%,#9cc8ea 40%,#2f6fc0 75%,#1b4d94)}
  .photo--microscope{left:241px;top:117px;width:278px;height:278px;background:radial-gradient(circle at 60% 40%,#e6f1fb 0 12%,#7fb2df 40%,#2d5f9e 75%,#18365f)}

  .brand-mark{position:absolute;display:flex;flex-direction:column;align-items:center;gap:10px;font-family:Montserrat,sans-serif;font-weight:600;color:var(--brand);text-align:center}
  .brand-mark .dot{width:84px;height:84px;border-radius:50%;border:4px solid var(--brand)}
  .brand-mark--back{left:76px;top:470px;width:200px;font-size:20px;line-height:1.2}

  .contact{position:absolute;font-family:Poppins,sans-serif;font-size:11px;color:var(--ink);line-height:13px}
  .contact li{list-style:none;display:flex;gap:6px;align-items:flex-start;margin-bottom:12px}
  .contact svg{flex:none;width:13px;height:13px;margin-top:0}
  .contact--left{left:85px;top:687px;width:230px}
  .contact--right{left:318px;top:687px;width:230px}

  .cover-text{position:absolute;left:570px;width:543px;text-align:center;color:#fff;font-family:Montserrat,sans-serif;text-shadow:0 3px 6px rgba(0,0,0,.45)}
  .cover-kicker{top:93px;font-size:17px;font-weight:600;letter-spacing:.2px}
  .cover-headline{top:155px}
  .cover-headline .lead{display:block;font-size:29px;font-weight:600;line-height:34px}
  .cover-headline .strong{display:block;font-size:64px;font-weight:900;line-height:70px;margin-top:2px}

  .seal{position:absolute;left:708px;top:394px;width:246px;height:246px;border-radius:50%;background:var(--paper);box-shadow:0 8px 20px rgba(0,0,0,.35);display:flex;align-items:center;justify-content:center}
  .seal .brand-mark{position:static;font-size:21px;line-height:1.2;width:170px}

  .cover-footer{position:absolute;left:570px;width:543px;top:731px;text-align:center;font-family:Poppins,sans-serif;font-size:12px;color:var(--ink);letter-spacing:.2px}
</style>
</head>
<body>
<main class="folder">
  <svg class="folder-art" viewBox="0 0 1120 1154" aria-hidden="true">
    <defs>
      <linearGradient id="sheetBlue" x1="0" y1="0" x2="1" y2="1">
        <stop offset="0" stop-color="#0b2a63"/>
        <stop offset=".5" stop-color="#163f85"/>
        <stop offset="1" stop-color="#1d55a3"/>
      </linearGradient>
      <linearGradient id="paperFade" x1="0" y1="0" x2="1" y2="0">
        <stop offset="0" stop-color="#ffffff"/>
        <stop offset=".5" stop-color="#f1f1f3"/>
        <stop offset="1" stop-color="#ffffff"/>
      </linearGradient>
      <linearGradient id="pocketBlue" x1="0" y1="0" x2="0" y2="1">
        <stop offset="0" stop-color="#0a2d63"/>
        <stop offset=".35" stop-color="#103f7a"/>
        <stop offset="1" stop-color="#1f78a8"/>
      </linearGradient>
    </defs>
    <rect x="0" y="0" width="1120" height="764" fill="url(#sheetBlue)" role="img" aria-label="Deep blue microscopic cell texture background"/>
    <path d="M0,424 C110,378 260,392 410,510 S650,706 800,712 S1050,662 1120,600" fill="none" stroke="#2a72c2" stroke-width="7"/>
    <path d="M0,412 C110,368 260,382 410,500 S650,696 800,702 S1050,652 1120,590 L1120,764 L0,764 Z" fill="url(#paperFade)"/>
    <path d="M0,764 L553,764 L553,890 Q553,962 488,986 L0,1154 Z" fill="url(#pocketBlue)"/>
  </svg>

  <div class="trim trim--back"></div>
  <div class="trim trim--front"></div>

  <div class="photo photo--sample" role="img" aria-label="Photo: gloved hand holding a petri dish with pink cultures"></div>
  <div class="photo photo--microscope" role="img" aria-label="Photo: lab scientist looking into a microscope"></div>

  <div class="brand-mark brand-mark--back">
    <span class="dot"></span>
    <span>Coastline Mobile Labs</span>
  </div>

  <ul class="contact contact--left">
    <li>
      <svg viewBox="0 0 14 14"><circle cx="7" cy="7" r="6" fill="none" stroke="#1f5fb5" stroke-width="1.3"/><ellipse cx="7" cy="7" rx="2.6" ry="6" fill="none" stroke="#1f5fb5" stroke-width="1"/><line x1="1" y1="7" x2="13" y2="7" stroke="#1f5fb5" stroke-width="1"/></svg>
      <span>www.coastlinemobilelabs.com</span>
    </li>
    <li>
      <svg viewBox="0 0 14 14"><circle cx="7" cy="7" r="6" fill="none" stroke="#1f5fb5" stroke-width="1.3"/><path d="M7 3.2a2.4 2.4 0 0 1 2.4 2.4c0 1.8-2.4 4.4-2.4 4.4S4.6 7.4 4.6 5.6A2.4 2.4 0 0 1 7 3.2z" fill="#1f5fb5"/></svg>
      <span>1480 Harbor Ridge Drive<br>Suite 210, Fairview, Oregon 97024</span>
    </li>
  </ul>
  <ul class="contact contact--right">
    <li>
      <svg viewBox="0 0 14 14"><circle cx="7" cy="7" r="6" fill="none" stroke="#1f5fb5" stroke-width="1.3"/><path d="M4.6 4c.4-.4.8-.3 1 .1l.6 1c.2.4 0 .7-.3.9.4.9 1 1.5 1.9 1.9.2-.3.5-.5.9-.3l1 .6c.4.2.5.6.1 1-.6.7-1.3.8-2 .5C6 9.1 4.9 8 4.4 6.3c-.3-.8-.2-1.6.2-2.3z" fill="#1f5fb5"/></svg>
      <span>(555) 014-2287</span>
    </li>
    <li>
      <svg viewBox="0 0 14 14"><circle cx="7" cy="7" r="6" fill="none" stroke="#1f5fb5" stroke-width="1.3"/><rect x="4" y="4.8" width="6" height="4.4" fill="none" stroke="#1f5fb5" stroke-width="1"/><path d="M4 4.8l3 2.4 3-2.4" fill="none" stroke="#1f5fb5" stroke-width="1"/></svg>
      <span>hello@coastlinemobilelabs.com</span>
    </li>
  </ul>

  <p class="cover-text cover-kicker">COASTLINE MOBILE LABS</p>
  <h1 class="cover-text cover-headline">
    <span class="lead">LABORATORY RESULTS THAT</span>
    <span class="strong">YOU CAN</span>
    <span class="strong">TRUST</span>
  </h1>

  <div class="seal">
    <div class="brand-mark">
      <span class="dot"></span>
      <span>Coastline Mobile Labs</span>
    </div>
  </div>

  <p class="cover-footer">LABORATORY AND PHLEBOTOMY SERVICES</p>
</main>
</body>
</html>
```